Stylish Business Cards Wanted

- DOUBLE SIDED Design Required -

High end, edgy cards for a corporate and personal stylist. Must include logo,
Name: Belinda Harwick
Title: Director and Stylist
telephone : +61 8 7142 5809
email: belinda@theloombriefing.example
website: theloombriefing.example
Tag: Corporate Workwear & Uniform Specialist | Personal Stylist
Would like nice icons for telephone, email, website

Target Market(s)

Businesses wanting stylish uniforms, people wanting stylish wardrobes

Industry/Entity Type

Corporate Workwear Stylist

Contact Information for Business Card

I would like black, white and gold foiling incorporated in the design - possibly a touch of the other colours on my branding guide attached Name: Belinda Harwick Title: Director and Stylist telephone : +61 8 7142 5809 email: belinda@theloombriefing.example website: theloombriefing.example Tag: Corporate Workwear & Uniform Specialist | Personal Stylist Would like nice icons for telephone, email, website

Font styles to use
Other font styles liked:
• Raleway

Colors

Designer to choose colors to be used in the design.

Requirements
Must have
• Gold foil accents

```html
<!DOCTYPE html>
<html lang="en">
<head>
<meta charset="utf-8">
<title>The Loom Briefing — Business Cards</title>
<link href="https://fonts.googleapis.com/css2?family=Raleway:wght@300;400;500;600&display=swap" rel="stylesheet">
<style>
  :root {
    --gold: #e3bc57;
    --ink: #231f20;
    --paper: #ffffff;
    --backdrop: #ececec;
    --mist: #f1f1f2;
  }
  * { box-sizing: border-box; margin: 0; padding: 0; }
  html, body {
    width: 1200px; height: 507px; overflow: hidden;
    background: var(--backdrop);
    font-family: "Raleway", sans-serif;
  }
  .stage { position: relative; width: 1200px; height: 507px; }
  .card {
    position: absolute; top: 106px;
    width: 493px; height: 295px;
    overflow: hidden;
  }
  .card--front { left: 83px; background: var(--gold); }
  .card--back { left: 624px; background: var(--paper); }

  .wordmark {
    font-family: "Raleway", sans-serif;
    font-weight: 600;
    color: var(--ink);
    letter-spacing: 0.5px;
    white-space: nowrap;
  }
  .card--front .wordmark {
    position: absolute; left: 0; right: 0; top: 118px;
    text-align: center; font-size: 30px;
  }
  .tagline {
    position: absolute; left: 0; right: 0; top: 210px;
    text-align: center; font-size: 14.5px; font-weight: 400;
    color: var(--ink);
  }
  .tagline .divider { margin: 0 5px; }

  .card--back .wordmark {
    position: absolute; left: 36px; top: 78px; font-size: 23px;
  }
  .backdrop-word {
    position: absolute; right: -6px; bottom: 8px;
    font-size: 96px; font-weight: 300; color: var(--mist);
    letter-spacing: -2px; line-height: 1;
  }
  .gold-sweep { position: absolute; left: 0; top: 0; }
  .holder { position: absolute; left: 36px; top: 160px; }
  .holder__name {
    font-size: 21px; font-weight: 300; color: var(--gold);
    letter-spacing: 0.3px; text-transform: uppercase; line-height: 1;
  }
  .holder__title {
    margin: 5px 0 0 3px; font-size: 10.5px; font-weight: 500; color: var(--ink);
  }
  .contacts { list-style: none; margin-top: 9px; }
  .contacts li {
    display: flex; align-items: center; gap: 6px;
    height: 20px; font-size: 13px; color: var(--ink);
  }
  .contacts svg { width: 10px; height: 10px; flex: none; }
</style>
</head>
<body>
<main class="stage">

  <section class="card card--front" aria-label="Card front">
    <div class="wordmark">The Loom Briefing</div>
    <p class="tagline">Corporate Workwear<span class="divider">|</span>Uniform Specialist<span class="divider">|</span>Personal Stylist</p>
  </section>

  <section class="card card--back" aria-label="Card back">
    <svg class="gold-sweep" width="493" height="295" viewBox="0 0 493 295" aria-hidden="true">
      <path d="M250 295 C 330 272, 420 268, 493 262 L 493 295 Z" fill="var(--gold)"/>
    </svg>
    <div class="backdrop-word" aria-hidden="true">loom</div>

    <div class="wordmark">The Loom Briefing</div>

    <div class="holder">
      <h1 class="holder__name">Belinda Harwick</h1>
      <p class="holder__title">Director and Stylist</p>
      <ul class="contacts">
        <li>
          <svg viewBox="0 0 10 10" aria-hidden="true"><circle cx="5" cy="5" r="5" fill="var(--gold)"/><path d="M2.6 4.6 Q5 2.6 7.4 4.6 L7 5.4 L6 5 L4 5 L3 5.4 Z M3.4 5.8 H6.6 V7.2 H3.4 Z" fill="#fff"/></svg>
          +61 8 7142 5809
        </li>
        <li>
          <svg viewBox="0 0 10 10" aria-hidden="true"><circle cx="5" cy="5" r="5" fill="var(--gold)"/><rect x="2.5" y="3.3" width="5" height="3.4" fill="#fff"/><path d="M2.5 3.3 L5 5.2 L7.5 3.3" fill="none" stroke="var(--gold)" stroke-width="0.6"/></svg>
          belinda@theloombriefing.example
        </li>
        <li>
          <svg viewBox="0 0 10 10" aria-hidden="true"><circle cx="5" cy="5" r="5" fill="var(--gold)"/><g fill="none" stroke="#fff" stroke-width="0.6"><circle cx="5" cy="5" r="2.8"/><ellipse cx="5" cy="5" rx="1.2" ry="2.8"/><path d="M2.2 5 H7.8"/></g></svg>
          theloombriefing.example
        </li>
      </ul>
    </div>
  </section>

</main>
</body>
</html>
```